Webdesign für Hersteller für Pack- und Palettieranlagen für den Getränke- und Lebensmittelbereich
Webdesign für Hersteller für Pack- und Palettieranlagen für den Getränke- und Lebensmittelbere..
Zielgruppe
Hersteller für Pack- und Palettieranlagen für den Getränke- und Lebensmittelbereich
Zielgruppe: Getränke- und Lebensmittelhersteller
Aufgabenstellung
die zukünftige Seite soll dynamischer und intuitiver werden
klare Strukturen, aber morderner als das jetztige Layout
Keine Kopie der alten Seite www.kolmatech.de!
Startseite soll aufgeräumter sein
Logo, Rufnummer, Mail, Social Media
Startseite mit großem Headerbild (Slider)

```html
<!DOCTYPE html>
<html lang="de">
<head>
<meta charset="utf-8">
<title>Veranta Maschinenbau</title>
<link href="https://fonts.googleapis.com/css2?family=Inter:wght@400;500;600;700;800&display=swap" rel="stylesheet">
<style>
:root{
  --green:#66b52f;
  --orange:#f39a2e;
  --dark:#4a4a4a;
  --text:#333;
  --light:#ebebeb;
  --white:#fff;
}
*{margin:0;padding:0;box-sizing:border-box}
html,body{width:1200px;height:2987px;overflow:hidden;background:var(--white)}
body{font-family:"Inter",sans-serif;color:var(--text);position:relative}
.abs{position:absolute}
/* header */
.logo{left:62px;top:32px;display:flex;align-items:center;gap:8px}
.logo .dot{width:24px;height:24px;border-radius:50%;background:var(--green)}
.logo .name{font-weight:800;font-size:28px;color:var(--green);line-height:1}
.logo .sub{font-weight:700;font-size:12px;color:#222;margin-top:2px}
.pill{top:44px;height:30px;border-radius:15px;background:var(--green);color:#fff;font-size:13px;font-weight:500;display:flex;align-items:center;justify-content:center;letter-spacing:.2px;white-space:nowrap}
.social{top:50px;right:72px;display:flex;gap:16px}
.social span{width:18px;height:18px;border-radius:50%;background:#444;display:block}
.nav{top:116px;left:181px;display:flex;gap:19px;font-size:12.5px;font-weight:400;white-space:nowrap}
.nav a{color:#222;text-decoration:none;padding-bottom:6px}
.nav a.active{border-bottom:2px solid var(--green)}
/* hero */
.hero{left:62px;top:153px;width:1066px;height:500px;border-radius:4px;background:linear-gradient(135deg,#c9d6dc 0%,#9fb4bd 35%,#e4ecef 60%,#7b8f92 100%)}
.hero-label{left:62px;top:456px;width:609px;height:101px;background:var(--green);border-radius:0 4px 4px 0;color:#fff;font-weight:800;font-size:38px;line-height:38px;padding:14px 0 0 44px}
/* products */
.section-title{width:1200px;text-align:center;font-weight:700;font-size:20px;letter-spacing:.5px}
.tabs{top:767px;left:338px;display:flex;gap:30px;font-size:12px;color:#333}
.tab{text-align:center;padding-bottom:8px}
.tab.active{border-bottom:2px solid var(--green)}
.tab svg{display:block;margin:0 auto 8px}
.grayband{left:0;top:1077px;width:1200px;height:781px;background:var(--light)}
.panel{left:62px;top:938px;width:1066px;height:208px;background:var(--dark);border-radius:4px}
.card{top:874px;width:226px;height:236px;border-radius:3px;overflow:hidden;box-shadow:0 4px 12px rgba(0,0,0,.15)}
.card .img{height:187px}
.card .lbl{height:49px;background:var(--green);color:#fff;font-weight:700;font-size:13px;display:flex;align-items:center;justify-content:center}
/* news */
.post-img{top:1233px;width:315px;height:280px;background:#fff;border-radius:4px;box-shadow:0 2px 10px rgba(0,0,0,.06)}
.meta{font-size:6px;color:#777}
.post-title{font-size:11px;font-weight:700;color:#222}
.post-body{width:320px;font-size:8.5px;line-height:9.5px;color:#444}
.news-list{left:814px;top:1232px}
.news-item{height:43.7px}
.btn{border-radius:3px;background:var(--green);color:#fff;font-weight:600;font-size:11px;display:flex;align-items:center;justify-content:center}
/* jobs */
.jobs{left:67px;top:1663px;width:1066px;height:387px;border-radius:6px;background:linear-gradient(120deg,#f29a34,#f08d22 60%,#f3a24a)}
.jobs h2{color:#fff;text-align:center;font-size:19px;font-weight:700;margin-top:26px}
.jobs p.lead{color:#fff;text-align:center;font-size:10.5px;line-height:12px;margin:27px auto 0;width:600px}
.jobtabs{display:flex;justify-content:center;gap:38px;font-size:11px;color:#ffd7a8;margin-top:37px}
.jobtabs .on{color:#fff;border-bottom:2px solid #fff;padding-bottom:6px}
.job{top:1858px;width:310px;height:146px;background:var(--dark);border-radius:4px;color:#fff;padding:10px 14px;box-shadow:0 4px 10px rgba(0,0,0,.2)}
.job .top{display:flex;justify-content:space-between;font-size:6px;color:#aaa}
.job h3{font-size:14px;font-weight:600;margin-top:6px}
.job .d{font-size:9px;line-height:11px;margin-top:3px;width:270px}
.job .s{font-size:6.5px;margin-top:8px}
.job .row{display:flex;gap:10px;position:absolute;bottom:14px;left:14px}
.job .row span{height:28px;border:1px solid #aaa;border-radius:3px;font-size:9px;display:flex;align-items:center;justify-content:center}
.job .row .ap{background:var(--green);border-color:var(--green);font-weight:600}
/* company */
.about{left:67px;top:2165px;width:470px;font-size:10.5px;line-height:11.5px;color:#444}
.about p{margin-bottom:11px}
.team{left:627px;top:2165px;width:506px;height:157px;border-radius:3px;background:linear-gradient(90deg,#9aa6ad,#c8cdd0 40%,#7f8b93 70%,#2d3d55)}
/* contact */
.contact{left:67px;top:2402px;width:1066px;height:342px;background:#fff;box-shadow:0 4px 20px rgba(0,0,0,.08);border-radius:4px;overflow:hidden}
.contact .img{position:absolute;left:0;top:0;width:506px;height:342px;background:linear-gradient(160deg,#2c3f6b,#4a5f8c 40%,#8a6a3a 75%,#c39a60)}
.contact h2{position:absolute;left:556px;top:26px;font-size:19px;font-weight:700}
.field{position:absolute;width:172px;border-bottom:1px solid #ddd;font-size:11px;color:#555;padding-bottom:8px}
.send{position:absolute;left:556px;top:282px;width:104px;height:34px;background:var(--orange);border-radius:3px;color:#fff;font-size:12px;font-weight:500;display:flex;align-items:center;justify-content:center;gap:10px}
/* footer */
.footer{left:0;top:2824px;width:1200px;height:163px;background:var(--dark);color:#fff}
.fh{font-weight:700;font-size:11px}
.fl{font-size:9.5px;line-height:20px}
.copy{position:absolute;left:0;bottom:0;width:1200px;border-top:1px solid #5c5c5c;text-align:center;font-size:9px;padding:9px 0 10px}
.nl{position:absolute;left:952px;top:54px;display:flex}
.nl .in{width:124px;height:26px;background:#fff;color:#555;font-size:8px;padding:8px}
.nl .go{width:30px;height:26px;background:var(--green);display:flex;align-items:center;justify-content:center}
</style>
</head>
<body>

<header>
  <div class="abs logo">
    <span class="dot"></span>
    <div><div class="name">VERANTA</div><div class="sub">Maschinenbau GmbH</div></div>
  </div>
  <div class="abs pill" style="left:670px;width:141px">030 4488 / 120 - 0</div>
  <div class="abs pill" style="left:832px;width:157px">INFO@VERANTA-MB.DE</div>
  <div class="abs social"><span></span><span></span><span></span><span></span></div>
  <nav class="abs nav">
    <a class="active">UNTERNEHMEN</a><a>JOBS / KARRIERE</a><a>PALETTIERTECHNIK</a><a>PACKERTECHNIK</a><a>FÖRDERTECHNIK</a><a>ANLAGEN</a><a>GEBRAUCHTMASCHINEN</a><a>AKTUELLES</a>
  </nav>
</header>

<section>
  <div class="abs hero" role="img" aria-label="Abfüllanlage mit grünen Glasflaschen"></div>
  <div class="abs hero-label">GETRÄNKE- UND<br>LEBENSMITTELHERSTELLER</div>
</section>

<div class="abs grayband"></div>

<section>
  <h2 class="abs section-title" style="top:712px;color:var(--green)">PRODUKTE</h2>
  <div class="abs tabs">
    <div class="tab active"><svg width="26" height="20"><rect x="2" y="2" width="22" height="10" fill="none" stroke="#66b52f" stroke-width="2"/><rect x="2" y="14" width="22" height="4" fill="#66b52f"/></svg>PALETTIERTECHNIK</div>
    <div class="tab"><svg width="20" height="20"><rect x="3" y="3" width="14" height="14" fill="#66b52f"/></svg>PACKERTECHNIK</div>
    <div class="tab"><svg width="26" height="20"><rect x="2" y="3" width="22" height="12" fill="#66b52f"/><circle cx="7" cy="17" r="2" fill="#66b52f"/><circle cx="19" cy="17" r="2" fill="#66b52f"/></svg>FÖRDERTECHNIK</div>
    <div class="tab"><svg width="20" height="20"><path d="M4 17 L14 7" stroke="#66b52f" stroke-width="2.5"/><circle cx="15" cy="6" r="3" fill="none" stroke="#66b52f" stroke-width="2"/></svg>GEBRAUCHTMASCHINEN</div>
  </div>
  <div class="abs panel"></div>
  <div class="abs card" style="left:91px"><div class="img" role="img" aria-label="Portalmaschine in Produktionshalle" style="background:linear-gradient(160deg,#6f9b7a,#2f7a55 50%,#b7c2b0)"></div><div class="lbl">PORTALMASCHINEN</div></div>
  <div class="abs card" style="left:351px"><div class="img" role="img" aria-label="Einsäulenmaschine mit Greifer" style="background:linear-gradient(160deg,#e4e6e8,#2b3c7a 50%,#8a8d92)"></div><div class="lbl">EINSÄULENMASCHINEN</div></div>
  <div class="abs card" style="left:611px"><div class="img" role="img" aria-label="Industrieroboter in Schutzzelle" style="background:linear-gradient(160deg,#c6cbd0,#d08a3a 50%,#5a6270)"></div><div class="lbl">INDUSTRIEROBOTER</div></div>
  <div class="abs card" style="left:871px"><div class="img" role="img" aria-label="Neuglasmaschine mit Kastenstapeln" style="background:linear-gradient(160deg,#b9c0c8,#59616d 55%,#2b2f36)"></div><div class="lbl">NEUGLASMASCHINEN</div></div>
</section>

<section>
  <h2 class="abs section-title" style="top:1173px;color:#444">AKTUELLES</h2>
  <div class="abs post-img" style="left:62px"></div>
  <div class="abs post-img" style="left:437px"></div>
  <div class="abs meta" style="left:62px;top:1526px">März 6, 2024 &nbsp;&nbsp;&nbsp; By VERANTA</div>
  <div class="abs post-title" style="left:62px;top:1537px">Just published my first Journal on the website!</div>
  <div class="abs post-body" style="left:62px;top:1561px">Lorem Ipsum Dolor Sit Amet, Consectetur Adipiscing Elit, Sed Do Eiusmod Tempor Incididunt Ut Labore Et Dolore Magna Aliqua. Ut Enim Ad Minim Veniam, Quis Nostrud Exercitation Ullamco Laboris Nisi Ut Aliquip Ex Ea Commodo Consequat. Duis Aute Irure Dolor In Reprehenderit In Voluptate Velit Esse Cillum Dolore Eu Fugiat Nulla Pariatur. Excepteur Sint Occaecat Cupidatat Non Proident, Sunt In Culpa Qui Officia Deserunt Mollit Anim Id Est Laborum.</div>
  <div class="abs meta" style="left:442px;top:1526px">März 6, 2024 &nbsp;&nbsp;&nbsp; By VERANTA</div>
  <div class="abs post-title" style="left:442px;top:1537px">Just published my first Journal on the website!</div>
  <div class="abs post-body" style="left:442px;top:1561px">Lorem Ipsum Dolor Sit Amet, Consectetur Adipiscing Elit, Sed Do Eiusmod Tempor Incididunt Ut Labore Et Dolore Magna Aliqua. Ut Enim Ad Minim Veniam, Quis Nostrud Exercitation Ullamco Laboris Nisi Ut Aliquip Ex Ea Commodo Consequat. Duis Aute Irure Dolor In Reprehenderit In Voluptate Velit Esse Cillum Dolore Eu Fugiat Nulla Pariatur. Excepteur Sint Occaecat Cupidatat Non Proident, Sunt In Culpa Qui Officia Deserunt Mollit Anim Id Est Laborum.</div>
  <div class="abs news-list">
    <div class="news-item"><div class="meta">März 6, 2024 &nbsp;&nbsp;&nbsp; By VERANTA</div><div class="post-title" style="margin-top:4px">Just published my first Journal on the website!</div></div>
    <div class="news-item"><div class="meta">März 6, 2024 &nbsp;&nbsp;&nbsp; By VERANTA</div><div class="post-title" style="margin-top:4px">Just published my first Journal on the website!</div></div>
    <div class="news-item"><div class="meta">März 6, 2024 &nbsp;&nbsp;&nbsp; By VERANTA</div><div class="post-title" style="margin-top:4px">Just published my first Journal on the website!</div></div>
    <div class="news-item"><div class="meta">März 6, 2024 &nbsp;&nbsp;&nbsp; By VERANTA</div><div class="post-title" style="margin-top:4px">Just published my first Journal on the website!</div></div>
    <div class="news-item"><div class="meta">März 6, 2024 &nbsp;&nbsp;&nbsp; By VERANTA</div><div class="post-title" style="margin-top:4px">Just published my first Journal on the website!</div></div>
    <div class="news-item"><div class="meta">März 6, 2024 &nbsp;&nbsp;&nbsp; By VERANTA</div><div class="post-title" style="margin-top:4px">Just published my first Journal on the website!</div></div>
    <div class="news-item"><div class="meta">März 6, 2024 &nbsp;&nbsp;&nbsp; By VERANTA</div><div class="post-title" style="margin-top:4px">Just published my first Journal on the website!</div></div>
    <div class="news-item"><div class="meta">März 6, 2024 &nbsp;&nbsp;&nbsp; By VERANTA</div><div class="post-title" style="margin-top:4px">Just published my first Journal on the website!</div></div>
  </div>
  <div class="abs btn" style="left:814px;top:1589px;width:144px;height:37px">ALLE NACHRICHTEN</div>
</section>

<section class="abs jobs">
  <h2>JOBS / KARRIERE</h2>
  <p class="lead">Schauen Sie Sich Jetzt Unsere Aktuellen Stellenangebote An Und Bewerben Sie Sich Ganz Einfach Auf Ihre Wunschstelle. Eine Bewerbung Läuft Ganz Einfach In 60 Sekunden Ab – Ohne Lebenslauf Oder Anschreiben.</p>
  <div class="jobtabs"><span class="on">Alle</span><span>Development</span><span>Marketing</span><span>Specialist</span></div>
</section>
<div class="abs job" style="left:249px">
  <div class="top"><span>März 6, 2024</span><span>Feldstadt, Germany</span></div>
  <h3>SPS-Programmierung</h3>
  <div class="d">Für Die Fertigung Unserer Einzel- Und Serienprodukte Im Bereich Getränkemaschinenbau Suchen Wir Eine/N Fachlich Versierte/N</div>
  <div class="s">SPS-Programmierer/In M/W/D</div>
  <div class="row"><span style="width:58px">€100K</span><span style="width:142px">Arbeitsbeschreibung</span><span class="ap" style="width:56px">Apply</span></div>
</div>
<div class="abs job" style="left:609px">
  <div class="top"><span>März 6, 2024</span><span>Feldstadt, Germany</span></div>
  <h3>Ausbildungsplätze</h3>
  <div class="d">Mechatroniker Und Feinwerkmechaniker</div>
  <div class="s" style="margin-top:14px">Feinwerkmechaniker (M/W/D)</div>
  <div class="s">Mechatroniker (M/W/D)</div>
  <div class="row"><span style="width:58px">N/A</span><span style="width:142px">Arbeitsbeschreibung</span><span class="ap" style="width:56px">Apply</span></div>
</div>

<section>
  <h2 class="abs section-title" style="top:2095px;color:#444">UNTERNEHMEN</h2>
  <div class="abs about">
    <p>Das Traditionsreiche Familienunternehmen Veranta Plant, Entwickelt Und Baut Pack- Und Palettieranlagen Für Den Getränke- Und Lebensmittelbereich. Mit Erfahrung Und Know-How Planen Und Konstruieren Wir Moderne Und Effiziente Anlagen, Die Optimal Auf Die Bedürfnisse Unserer Kunden Abgestimmt Sind.</p>
    <p>Wir Bieten Ihnen Individuelle Maschinen Und Anlagen Zur Abfüllung Und Verpackung, Sortier- Und Umpackanlagen Sowie Einen Umfassenden Rundum-Service An. Mit Unseren Weitläufigen Produktionsstätten Sind Wir In Der Lage, Die Vorarbeiten Der Montage Unter Unserem Dach Zu Erledigen, Sodass Der Zeitaufwand Für Den Aufbau Bei Ihnen Vor Ort Gering Ist.</p>
    <p>Die Wartung Der Anlagen Und Ein Ersatzteil-Service Sowie Professionelle Unterstützung Und Hilfestellung Bei Problemen Sind Für Uns Selbstverständliche Dienstleistungen.</p>
  </div>
  <div class="abs team" role="img" aria-label="Team in der Werkstatt beim Händeschütteln"></div>
</section>

<section class="abs contact">
  <div class="img" role="img" aria-label="Produktionshalle mit Holzpaletten und Stahlanlagen"></div>
  <h2>KONTAKT</h2>
  <div class="field" style="left:556px;top:92px">Vorname</div>
  <div class="field" style="left:765px;top:92px">Nachname</div>
  <div class="field" style="left:556px;top:140px">Email</div>
  <div class="field" style="left:765px;top:140px">Telefonnummer</div>
  <div class="field" style="left:556px;top:228px;width:381px">Schreibe deine Nachricht...</div>
  <div class="send"><svg width="14" height="14"><path d="M1 7 L13 1 L9 13 L7 8 Z" fill="#fff"/></svg>Senden</div>
</section>

<footer class="abs footer">
  <div class="abs fh" style="left:52px;top:30px">QUICKLINKS</div>
  <div class="abs fl" style="left:52px;top:48px">Unternehmen<br>Jobs / Karriere<br>Palettiertechnik</div>
  <div class="abs fl" style="left:144px;top:48px">Packertechnik<br>Fördertechnik<br>Anlagen</div>
  <div class="abs fl" style="left:228px;top:48px">Gebrauchtmaschinen<br>Aktuelles</div>
  <div class="abs fh" style="left:361px;top:30px">PRODUKTE</div>
  <div class="abs fl" style="left:361px;top:48px">PALETTIERTECHNIK<br>PACKERTECHNIK</div>
  <div class="abs fl" style="left:473px;top:48px">FÖRDERTECHNIK<br>GEBRAUCHTMASCHINEN</div>
  <div class="abs fh" style="left:625px;top:30px">KONTAKT</div>
  <div class="abs" style="left:625px;top:50px;font-size:9.5px;line-height:12px">VERANTA Maschinenbau GmbH<br>Am Werkhof 12<br>09123 Feldstadt</div>
  <div class="abs fl" style="left:791px;top:48px">030 4488 / 120 - 0<br>030 4488 / 120 - 14<br>info@veranta-mb.de</div>
  <div class="abs" style="left:952px;top:37px;font-size:8.5px;font-weight:600">Abonnieren Sie den Newsletter</div>
  <div class="nl"><div class="in">Email</div><div class="go"><svg width="12" height="10"><path d="M0 5 H10 M6 1 L10 5 L6 9" stroke="#fff" stroke-width="2" fill="none"/></svg></div></div>
  <div class="copy">©2024. Veranta All rights reserved</div>
</footer>

</body>
</html>
```